Redesign a Start-Up Dating Website

Website: https://morvelique.com.
Make sure the design has an island style theme.
I would like the 7 pages of my website to have a new and professional look. I want the same colors to remain, but I want a creative look for all the pages. This is a dating website that is in the startup stage. So, I want to give my entire website a custom makeover. I want something that will stand out from the other dating sites. Something that will attract more people to want to use my services, and hopefully get new members.
Target Market(s)
Dating
Industry/Entity Type
Dating
Coding
Coded - Design and coding required
Number of Pages Required
5+ page
Font styles to use
Other font styles liked:
- Decorative, San Serif
Requirements
Must have
- The design must have the original colors and a stylish font to go along. The design must be creative, welcoming, and professional. I would like an island style theme for the website. This is a dating website so make sure that the design is tailored to that aspect.
Nice to have
- It would be nice to have a decorative font and a professional style on all the pages. Make sure the design will be mobile responsive and friendly for all the pages on the website.
Should not have
- The design should not be bland and uncreative.

```html
<!DOCTYPE html>
<html lang="en">
<head>
<meta charset="utf-8">
<title>Morvelique – Online Dating Made Easy</title>
<link href="https://fonts.googleapis.com/css2?family=Lato:wght@400;700;900&family=Open+Sans:wght@400;600&display=swap" rel="stylesheet">
<style>
:root{
  --purple:#6a3d9a;
  --purple-dark:#552f80;
  --orange:#f6a21e;
  --teal:#3fc3b2;
  --teal-dark:#2fae9f;
  --ink:#3a3a3a;
  --muted:#9a9a9a;
  --line:#e4e4e4;
  --white:#ffffff;
}
*{box-sizing:border-box;margin:0;padding:0}
html,body{width:1200px;height:3828px;overflow:hidden}
body{font-family:"Open Sans",Arial,sans-serif;color:var(--ink);background:var(--white);position:relative}
h1,h2,h3,h4,.brand,.nav,.btn{font-family:"Lato",Arial,sans-serif}
.abs{position:absolute}

/* header */
.topbar{left:660px;top:0;width:540px;height:30px;background:var(--orange);clip-path:polygon(24px 0,100% 0,100% 100%,0 100%);display:flex;align-items:center;justify-content:flex-end;gap:34px;padding-right:40px;color:#fff;font-size:12px;font-weight:600}
.topbar span{display:flex;align-items:center;gap:6px}
.brand{display:flex;align-items:center;gap:10px;font-weight:900;font-size:34px;color:var(--purple)}
.brand i{display:block;width:34px;height:34px;border-radius:50%;background:var(--orange)}
.site-brand{left:60px;top:34px}
.nav{right:60px;top:56px;display:flex;gap:26px;font-size:13px;font-weight:700;color:#555;letter-spacing:.5px}
.nav a:first-child{color:var(--purple)}

/* hero */
.hero{left:0;top:112px;width:1200px;height:680px;background:linear-gradient(110deg,#3b2418 0%,#7a4a2e 35%,#b06b3a 60%,#4a2a1c 100%)}
.hero-title{left:60px;top:360px;color:#fff;font-weight:900;font-size:54px;line-height:1.08;letter-spacing:1px}
.arrow{top:370px;width:20px;height:40px;color:#fff;font-size:30px;line-height:40px;text-align:center;font-family:Lato,sans-serif}
.quick-search{left:720px;top:200px;width:380px;height:350px;background:var(--purple);border:4px solid var(--orange);padding:26px 28px;color:#fff;text-align:center}
.quick-search h3{font-size:24px;font-weight:900;letter-spacing:1px}
.quick-search p{font-size:11px;margin:8px 30px 18px;line-height:1.5;opacity:.9}
.fields{display:grid;grid-template-columns:1fr 1fr;gap:12px}
.field{height:34px;background:#fff;border-radius:2px;color:#999;font-size:11px;text-align:left;padding:9px 10px}
.field.full{grid-column:1/3}
.btn{display:inline-block;font-weight:700;font-size:12px;letter-spacing:1px;color:#fff;padding:10px 26px;border-radius:3px}
.btn-teal{background:var(--teal)}
.btn-ghost{border:2px solid #fff}
.quick-search .btn{margin-top:16px}

/* sections */
.section-title{left:0;width:1200px;text-align:center;font-weight:900;font-size:30px;color:var(--purple);letter-spacing:.5px}
.lead{left:300px;width:600px;text-align:center;font-size:12px;color:var(--muted);line-height:1.7}
.steps{left:100px;top:1040px;width:1000px;display:grid;grid-template-columns:repeat(4,1fr);text-align:center}
.step .icon{width:120px;height:120px;border-radius:50%;background:var(--orange);margin:0 auto;display:flex;align-items:center;justify-content:center;box-shadow:0 0 0 8px #fde9c7}
.step h4{margin-top:28px;font-size:15px;font-weight:900;color:#333}
.step p{margin:10px 30px 0;font-size:11px;color:var(--muted);line-height:1.6}

.band{left:0;top:1352px;width:1200px;height:410px;background:var(--teal)}
.band-photo{left:0;top:1352px;width:620px;height:410px;background:linear-gradient(100deg,#2c1c18,#7b4a33 55%,#c08a5c);border-radius:0 50% 50% 0/0 50% 50% 0;border-right:8px solid var(--orange)}
.band-copy{left:672px;top:1450px;color:#fff}
.band-copy h2{font-size:46px;font-weight:900;line-height:1.1}
.band-copy p{font-size:12px;width:380px;margin:20px 0 24px;line-height:1.6;opacity:.9}

.profiles{left:100px;top:2072px;width:1000px;display:grid;grid-template-columns:repeat(5,1fr);text-align:center}
.avatar{width:160px;height:160px;border-radius:50%;margin:0 auto;border:6px solid var(--orange);background:linear-gradient(135deg,#d9b48f,#7aa6c2)}
.profile:nth-child(even) .avatar{border-color:var(--teal);background:linear-gradient(135deg,#9fc6e0,#c49a7a)}
.profile h4{margin-top:18px;font-size:13px;font-weight:900;color:#333}
.profile span{font-size:11px;color:var(--muted)}

.couples{left:0;top:2392px;width:1200px;height:372px;background:linear-gradient(90deg,#b5702a,#e4a550 50%,#b5702a)}
.couples-copy{left:0;top:2470px;width:1200px;text-align:center;color:#fff}
.couples-copy h2{font-size:40px;font-weight:900;line-height:1.2}
.couples-copy .btn{margin-top:26px}

.blogs{left:108px;top:2900px;width:992px;display:grid;grid-template-columns:repeat(3,1fr);gap:30px}
.blog-photo{height:300px;background:linear-gradient(135deg,#c9a183,#6c4a3c)}
.blog:nth-child(2) .blog-photo{background:linear-gradient(135deg,#e7c7b8,#a23b3b)}
.blog:nth-child(3) .blog-photo{background:linear-gradient(135deg,#8aa0b8,#3b2d2d)}
.blog-head{display:flex;gap:12px;align-items:center;margin-top:22px}
.blog-head h4{font-size:16px;font-weight:900;color:#333}
.blog-head small{display:block;font-size:10px;color:var(--muted);margin-top:3px}
.blog p{font-size:11px;color:var(--muted);line-height:1.7;margin-top:14px}

/* footer */
.footer{left:0;top:3420px;width:1200px;height:408px}
.footer-brand{left:0;top:3520px;width:1200px;justify-content:center;color:#fff}
.footer-brand i{background:var(--orange)}
.footer-cols{left:100px;top:3610px;width:1000px;display:grid;grid-template-columns:1.2fr 1fr 1fr 1.4fr;color:#fff}
.footer-cols h4{font-size:14px;font-weight:900;margin-bottom:14px}
.footer-cols li{list-style:none;font-size:11px;margin-bottom:8px;opacity:.9;display:flex;gap:8px;align-items:center}
.newsletter{display:flex;height:30px;background:#fff;border-radius:15px;overflow:hidden;width:260px}
.newsletter span{flex:1;font-size:10px;color:#999;padding:9px 12px}
.newsletter b{background:var(--teal);font-size:10px;color:#fff;padding:9px 16px}
.socials{display:flex;gap:10px;margin-top:14px}
.socials i{width:28px;height:28px;border-radius:50%;border:2px solid #fff;display:block}
.copyright{left:0;top:3780px;width:1200px;border-top:1px solid rgba(255,255,255,.2);padding-top:14px;text-align:center;font-size:11px;color:#fff;opacity:.85}
</style>
</head>
<body>

<header>
  <div class="abs topbar">
    <span>&#9742; +1 212 555 0148</span><span>&#128274; Login</span><span>&#10010; Register</span>
  </div>
  <div class="abs brand site-brand"><i></i>Morvelique</div>
  <nav class="abs nav"><a>HOME</a><a>SEARCH</a><a>MEMBERS</a><a>EXTRAS</a><a>ABOUT</a><a>PREMIUM</a><a>CONTACT</a></nav>
</header>

<section>
  <div class="abs hero" role="img" aria-label="Couple embracing at an evening party, warm light"></div>
  <div class="abs arrow" style="left:14px">&#8249;</div>
  <div class="abs arrow" style="right:14px">&#8250;</div>
  <h1 class="abs hero-title">ONLINE DATING<br>MADE EASY</h1>
  <form class="abs quick-search">
    <h3>QUICK SEARCH</h3>
    <p>Let's find your perfect match today, fill out the form below to begin</p>
    <div class="fields">
      <div class="field">Gender</div><div class="field">Looking for</div>
      <div class="field">Age</div><div class="field">To</div>
      <div class="field full">Select Country</div>
    </div>
    <span class="btn btn-teal">SEARCH</span>
  </form>
  <svg class="abs" style="left:0;top:690px" width="1200" height="110" viewBox="0 0 1200 110">
    <path d="M0 60 Q600 140 1200 40 L1200 110 L0 110Z" fill="#fff"/>
    <path d="M0 56 Q600 132 1200 34" fill="none" stroke="#f6a21e" stroke-width="6"/>
    <path d="M0 70 Q600 146 1200 48" fill="none" stroke="#3fc3b2" stroke-width="5"/>
  </svg>
</section>

<section>
  <h2 class="abs section-title" style="top:870px">STEP TO FIND YOUR SOUL MATE</h2>
  <p class="abs lead" style="top:930px">Every great story starts with a single hello. Create your profile, meet kind people nearby and let our simple steps guide you to someone who truly fits your life.</p>
  <div class="abs steps">
    <div class="step">
      <div class="icon"><svg width="48" height="48" viewBox="0 0 48 48" fill="#fff"><circle cx="24" cy="16" r="9"/><path d="M8 42c0-10 7-15 16-15s16 5 16 15z"/></svg></div>
      <h4>CREATE PROFILE</h4><p>Add your photos and a few words about you to start.</p>
    </div>
    <div class="step">
      <div class="icon"><svg width="48" height="48" viewBox="0 0 48 48" fill="#fff"><rect x="10" y="22" width="28" height="20" rx="3"/><path d="M16 22v-6a8 8 0 0 1 16 0v6" fill="none" stroke="#fff" stroke-width="4"/></svg></div>
      <h4>COMMUNICATE SECURELY</h4><p>Chat privately with members in a safe, friendly space.</p>
    </div>
    <div class="step">
      <div class="icon"><svg width="48" height="48" viewBox="0 0 48 48"><circle cx="21" cy="21" r="11" fill="none" stroke="#fff" stroke-width="5"/><path d="M29 29l11 11" stroke="#fff" stroke-width="6" stroke-linecap="round"/></svg></div>
      <h4>FIND MATCHES</h4><p>Browse people who share your goals and interests.</p>
    </div>
    <div class="step">
      <div class="icon"><svg width="48" height="48" viewBox="0 0 48 48" fill="#fff"><path d="M24 42 8 26a9 9 0 0 1 16-12 9 9 0 0 1 16 12z"/></svg></div>
      <h4>START DATING</h4><p>Meet up, share a sunset and see where it leads.</p>
    </div>
  </div>
</section>

<section>
  <div class="abs band"></div>
  <svg class="abs" style="left:960px;top:1370px" width="220" height="380" viewBox="0 0 220 380" fill="rgba(255,255,255,.15)">
    <path d="M110 120 60 70a30 30 0 0 1 50-34 30 30 0 0 1 50 34z"/>
    <path d="M60 330 30 300a18 18 0 0 1 30-20 18 18 0 0 1 30 20z"/>
    <path d="M180 260 160 240a12 12 0 0 1 20-14 12 12 0 0 1 20 14z"/>
  </svg>
  <div class="abs band-photo" role="img" aria-label="Couple toasting with glasses of red wine"></div>
  <div class="abs band-copy">
    <h2>START DATING<br>WITH MORVELIQUE</h2>
    <p>Sign up in a few minutes and join a warm community of singles ready to meet someone special on the island of love.</p>
    <span class="btn btn-ghost">VIEW DETAILS</span>
  </div>
</section>

<section>
  <h2 class="abs section-title" style="top:1910px">MEET YOUR LOVE PROFILES</h2>
  <p class="abs lead" style="top:1968px">Take a look at some of our newest members and say hello to the ones who catch your eye today.</p>
  <div class="abs profiles">
    <div class="profile"><div class="avatar" role="img" aria-label="Member portrait"></div><h4>NORA VALE</h4><span>Age: 26, F, USA</span></div>
    <div class="profile"><div class="avatar" role="img" aria-label="Member portrait"></div><h4>ARIA SOLEN</h4><span>Age: 24, F, USA</span></div>
    <div class="profile"><div class="avatar" role="img" aria-label="Member portrait"></div><h4>MILA ROWAN</h4><span>Age: 27, F, USA</span></div>
    <div class="profile"><div class="avatar" role="img" aria-label="Member portrait"></div><h4>THEO MARLIN</h4><span>Age: 29, M, USA</span></div>
    <div class="profile"><div class="avatar" role="img" aria-label="Member portrait"></div><h4>ISLA BRENNER</h4><span>Age: 25, F, USA</span></div>
  </div>
</section>

<section>
  <div class="abs couples" role="img" aria-label="Couple sitting together in a golden field at sunset"></div>
  <div class="abs couples-copy">
    <h2>MORE THAN 1000 HAPPY COUPLES<br>EVERY MONTH</h2>
    <span class="btn btn-ghost">VIEW DETAILS</span>
  </div>
</section>

<section>
  <h2 class="abs section-title" style="top:2820px">OUR LOVABLE BLOGS</h2>
  <div class="abs blogs">
    <article class="blog">
      <div class="blog-photo" role="img" aria-label="Couple sharing a picnic outdoors"></div>
      <div class="blog-head"><svg width="44" height="40" viewBox="0 0 44 40"><path d="M22 38 4 20a10 10 0 0 1 18-12 10 10 0 0 1 18 12z" fill="#f6a21e"/></svg><div><h4>Blog Post Title Here</h4><small>12 Comments · 8 Likes</small></div></div>
      <p>Simple tips for a relaxed first date by the sea, from choosing the spot to keeping the talk easy.</p>
    </article>
    <article class="blog">
      <div class="blog-photo" role="img" aria-label="Couple holding a bouquet of red roses"></div>
      <div class="blog-head"><svg width="44" height="40" viewBox="0 0 44 40"><path d="M22 38 4 20a10 10 0 0 1 18-12 10 10 0 0 1 18 12z" fill="#f6a21e"/></svg><div><h4>Blog Post Title Here</h4><small>9 Comments · 5 Likes</small></div></div>
      <p>How small gestures build trust early on, and why flowers still work after all these years.</p>
    </article>
    <article class="blog">
      <div class="blog-photo" role="img" aria-label="Couple taking a selfie in a winter city"></div>
      <div class="blog-head"><svg width="44" height="40" viewBox="0 0 44 40"><path d="M22 38 4 20a10 10 0 0 1 18-12 10 10 0 0 1 18 12z" fill="#f6a21e"/></svg><div><h4>Blog Post Title Here</h4><small>15 Comments · 11 Likes</small></div></div>
      <p>Travel ideas for new couples who want fun, shared memories without a big budget.</p>
    </article>
  </div>
</section>

<footer>
  <svg class="abs footer" viewBox="0 0 1200 408" width="1200" height="408">
    <path d="M0 40 Q600 -20 1200 40 L1200 408 L0 408Z" fill="#6a3d9a"/>
    <path d="M0 30 Q600 -30 1200 30" fill="none" stroke="#f6a21e" stroke-width="6"/>
    <path d="M0 44 Q600 -16 1200 44" fill="none" stroke="#3fc3b2" stroke-width="5"/>
  </svg>
  <div class="abs brand footer-brand"><i></i>Morvelique</div>
  <div class="abs footer-cols">
    <div>
      <h4>CONTACT US</h4>
      <ul>
        <li>&#9873; 250 Harbor Street, Suite 12</li>
        <li>&#9742; +1 212 555 0148</li>
        <li>&#9993; hello@morvelique.com</li>
      </ul>
    </div>
    <div>
      <h4>QUICK LINKS</h4>
      <ul><li>&#8250; Home</li><li>&#8250; About Us</li><li>&#8250; Dating</li><li>&#8250; Benefits</li></ul>
    </div>
    <div>
      <h4>MEMBERS</h4>
      <ul><li>&#8250; Members</li><li>&#8250; Login</li><li>&#8250; Register</li><li>&#8250; Reviews</li></ul>
    </div>
    <div>
      <h4>NEWSLETTER SIGN UP</h4>
      <div class="newsletter"><span>Enter your email</span><b>Subscribe</b></div>
      <div class="socials"><i></i><i></i><i></i><i></i></div>
    </div>
  </div>
  <div class="abs copyright">© Copyright 2017 Morvelique · All Rights Reserved · Terms &amp; Conditions</div>
</footer>

</body>
</html>
```